Church needs a street sign design

We're a small church located in Silicon Valley, California. Our website is https://www.vgtmarlowfield.org/ and our address is 4817 Ferrow Ave, San Jose, California, 95873. You can look up our location on Google Maps to see the sign from Street View. I have uploaded an image of the street sign as well. The marquee, the top section of the sign, and the separating line between them both will be removed. We're seeking a design for a new backlit acrylic insert that will go on the front of the light box and the back of the lightbox. The acrylic sign will fill the entire external frame. In the future, we may build a decorative wood frame around the structural legs, as visualized in one of the uploaded files. The church's brand colors are: #003366 (dark blue), #ff6600 (vibrant orange), #228b22 (forest green). I have also uploaded the church's logo assets. Our primary font is Montserrat and the secondary is Poppins. You can deviate from these colors/fonts if the sign is still coherent with the rest of our branding. Our branding values are mission, truth, passion, and community (please do not put those words on the sign! They are just intended to guide the look of the design). The sign dimensions are 96" by 47.5". Keep in mind that the sign will be backlit on a busy street side. It will also be positioned next to an old-looking church building. We do NOT want a sign that looks traditional, old, or antiquated. Instead, we want a modern-looking sign that pairs well with our old building while helping it look more modern too. We would also like the web address clearly visible on the sign: vgtmarlowfield.org. If you have any questions, just let me know!

```html
<!DOCTYPE html>
<html lang="en">
<head>
<meta charset="utf-8">
<title>Valley Grace Tabernacle – Street Sign</title>
<link rel="stylesheet" href="https://fonts.googleapis.com/css2?family=Montserrat:wght@500;600&family=Poppins:wght@600;700&display=swap">
<style>
  :root {
    --brand-navy: #0a3466;
    --brand-orange: #ff6600;
    --text-white: #ffffff;
    --photo-deep: #0a4878;
    --photo-light: #11639b;
  }
  html, body {
    margin: 0;
    padding: 0;
    width: 1200px;
    height: 594px;
    overflow: hidden;
    background: var(--brand-navy);
  }
  .sign {
    position: relative;
    width: 1200px;
    height: 594px;
    background: var(--brand-navy);
    overflow: hidden;
  }
  .sign__message {
    position: absolute;
    left: 0;
    top: 0;
    width: 778px;
    height: 594px;
  }
  .sign__building-photo {
    position: absolute;
    left: 778px;
    top: 0;
    width: 422px;
    height: 594px;
    background: linear-gradient(160deg, var(--photo-light) 0%, var(--photo-deep) 100%);
  }
  .invite {
    font-family: "Montserrat", sans-serif;
    font-weight: 600;
    font-size: 38px;
    letter-spacing: 10px;
    fill: var(--text-white);
  }
  .church-name {
    font-family: "Montserrat", sans-serif;
    font-weight: 600;
    fill: var(--text-white);
  }
  .church-name--primary { font-size: 122px; }
  .church-name--secondary { font-size: 43px; }
  .brand-mark { fill: var(--brand-orange); }
  .service-time {
    font-family: "Poppins", sans-serif;
    font-weight: 700;
    font-size: 27px;
    letter-spacing: 2px;
    fill: var(--brand-orange);
  }
  .web-address {
    font-family: "Poppins", sans-serif;
    font-weight: 600;
    font-size: 28px;
    letter-spacing: 3px;
    fill: var(--text-white);
  }
</style>
</head>
<body>
  <main class="sign">
    <svg class="sign__message" viewBox="0 0 778 594" xmlns="http://www.w3.org/2000/svg">
      <defs>
        <path id="invite-arc" d="M63,380 A293,293 0 0 1 649,380"/>
        <path id="address-arc" d="M105,297 A251,251 0 0 0 607,297"/>
      </defs>

      <text class="invite" text-anchor="middle">
        <textPath href="#invite-arc" startOffset="50%">JOIN US</textPath>
      </text>

      <rect class="brand-mark" x="344" y="140" width="24" height="24"/>

      <text class="church-name church-name--primary" x="121" y="326" textLength="472" lengthAdjust="spacingAndGlyphs">VALLEY</text>
      <text class="church-name church-name--secondary" x="121" y="382" textLength="466" lengthAdjust="spacingAndGlyphs">GRACE TABERNACLE</text>

      <text class="service-time" x="356" y="444" text-anchor="middle">SUNDAY SERVICE</text>
      <text class="service-time" x="359" y="476" text-anchor="middle">10:40 AM</text>

      <text class="web-address" text-anchor="middle">
        <textPath href="#address-arc" startOffset="50%">www.vgtmarlowfield.org</textPath>
      </text>
    </svg>

    <div class="sign__building-photo" role="img" aria-label="Blue-toned photo of the church's stone-faced gable with a tall narrow window, white steeple and shrubs in front"></div>
  </main>
</body>
</html>
```